Health and Fitness Club requires a stunning and simple website

We are a health and fitness club based in Dubai, when we launch we will be the biggest club in the country, we will also have the 2 largest activity rooms in the country, we are setting a new standard in the industry by offering one thing, our attitude.

Our attitude means the following:
unlike other clubs we have no hidden charges or fees
our members can join daily, monthly, 6 months or annually
our service and facility are comparable to 5* hotel gyms
our equipment is second to none
our space is the biggest in the country
we do not force our members to use our in-house personal trainers - you can bring your own and we will not charge them entry!
we will have a cutting edge brawnmesh box in our gym with classes by the best trainers in the country
we will be providing free-lance personal trainers a platform to engage customers, grow their business and even use our activity rooms for classes

Basically we will be a gym like no other, simply because we are gym people and we hate the restrictive practices and hidden charges by other gyms, so we are making our own gym which focuses on quality and service.

All of this has to be communicated in the style of the website, the colors of the website we want to be limited to the logo colors as this will be the same theme running throughout the gym.

The landing page of the website HAS to incorporate elements from our social media presences, this basically is the usual, chirplo, snapvault, kinwall. We can have these as a sidebar, the centre of the page should display the latest article from our blog (also on the website) Also we need to have a calendar for activities and classes on the front page. The menu should have links to the following:
Latest News
About us
Team
Gallery
Membership
Classes
Member Log In
Contact Us
Location

The style of the website has to be similar to the logo, particularly in terms of the fonts used.

```html
<!DOCTYPE html>
<html lang="en">
<head>
<meta charset="utf-8">
<title>Corevo Health &amp; Fitness Club</title>
<link href="https://fonts.googleapis.com/css2?family=Oswald:wght@400;500;700&family=Open+Sans:wght@400;600;700&display=swap" rel="stylesheet">
<style>
:root{
  --red:#d4242a;
  --red-dark:#a8181d;
  --green:#7cb82f;
  --green-dark:#5b8f1c;
  --ink:#222222;
  --bar:#2a2a2a;
  --text:#555555;
  --muted:#8a8a8a;
  --line:#dddddd;
  --panel:#f1f1f1;
  --white:#ffffff;
  --orange:#f39214;
  --violet:#8b6cc0;
  --head:'Oswald',sans-serif;
  --body:'Open Sans',sans-serif;
}
*{box-sizing:border-box;margin:0;padding:0}
html,body{width:759px;height:1200px;overflow:hidden}
body{font-family:var(--body);color:var(--text);background:var(--white);position:relative;font-size:8px;line-height:1.5}
.topbar{height:22px;background:var(--bar);color:#cfcfcf;display:flex;align-items:center;justify-content:space-between;padding:0 40px 0 130px;font-size:7.5px}
.topbar .contact{display:flex;gap:14px;align-items:center}
.topbar .contact span{display:flex;align-items:center;gap:4px}
.topbar .tools{display:flex;gap:6px;align-items:center}
.search{width:90px;height:13px;background:#444;border:1px solid #555}
.login{background:var(--orange);color:var(--white);padding:1px 9px;font-weight:700}
.header{height:53px;background:var(--white);position:relative;border-bottom:4px solid var(--red)}
.brand{position:absolute;left:48px;top:-14px;width:78px;height:78px;border-radius:50%;background:var(--white);border:3px solid var(--ink);display:flex;align-items:center;justify-content:center;z-index:3;box-shadow:0 0 0 3px var(--white)}
.brand-name{font-family:var(--head);font-weight:700;font-size:15px;color:var(--red);letter-spacing:.5px}
.nav{position:absolute;left:215px;right:0;top:6px;height:28px;background:#111;display:flex;align-items:center;padding-left:6px}
.nav a{color:var(--white);text-decoration:none;font-family:var(--head);font-size:8.5px;padding:0 10px;height:28px;line-height:28px}
.nav a.active{background:var(--red)}
.hero{height:340px;position:relative;background:linear-gradient(100deg,#c9d3d8 0%,#e8ecee 35%,#b8c3c9 65%,#8d9aa3 100%)}
.hero-photo{position:absolute;inset:0}
.arrow{position:absolute;top:160px;width:18px;height:26px;background:rgba(0,0,0,.75);display:flex;align-items:center;justify-content:center}
.arrow.left{left:0}.arrow.right{right:0}
.promo{position:absolute;top:210px;left:139px;display:flex;height:122px}
.promo-box{width:190px;padding:10px 12px}
.upcoming{background:var(--white);box-shadow:0 1px 4px rgba(0,0,0,.2)}
.upcoming h3{font-family:var(--head);font-weight:500;font-size:12px;color:var(--green-dark);line-height:1.1}
.upcoming small{display:block;font-size:7px;color:var(--muted);margin-bottom:6px}
.class-row{display:flex;justify-content:space-between;border-bottom:1px solid #eee;padding:3px 0;font-size:7.5px}
.class-row b{color:var(--ink);font-weight:600;display:flex;align-items:center;gap:5px}
.class-row b::before{content:"";width:8px;height:8px;background:var(--green)}
.offer{background:var(--green);color:var(--white)}
.offer:nth-child(3){width:202px}
.offer h3{font-family:var(--head);font-weight:400;font-size:15px;line-height:1.1}
.offer small{display:block;font-size:7px;opacity:.9;margin-bottom:6px}
.offer .detail{background:var(--green-dark);padding:6px 8px;font-size:7px;line-height:1.4;display:flex;gap:8px;align-items:flex-end;justify-content:space-between}
.more{background:#1c1c1c;color:var(--white);padding:2px 8px;font-size:7px;flex-shrink:0}
.social-rail{position:absolute;right:0;top:440px;display:flex;flex-direction:column;gap:2px;z-index:4}
.social-rail span{display:block;background:var(--red);color:var(--white);font-size:6.5px;font-weight:700;padding:3px 5px;text-align:right}
.social-rail span:nth-child(2){background:#3b5998}
.social-rail span:nth-child(3){background:#1da1f2}
.social-rail span:nth-child(4){background:#0e76a8}
.welcome{text-align:center;padding:30px 80px 24px}
.welcome h1{font-family:var(--head);font-weight:500;font-size:15px;color:var(--ink)}
.welcome h1 em{font-style:normal;color:var(--red)}
.welcome p{font-size:7.5px;color:var(--muted);margin-top:6px}
.middle{background:var(--panel);height:290px;padding:14px 48px 0 50px;display:flex;gap:22px}
.section-title{font-family:var(--head);font-weight:500;font-size:14px;color:var(--ink);margin-bottom:10px}
.section-title em{font-style:normal;color:var(--red)}
.news{width:445px}
.news-grid{display:grid;grid-template-columns:repeat(3,1fr);gap:10px 14px}
.card{background:var(--white);padding:5px;height:117px;box-shadow:0 1px 2px rgba(0,0,0,.08)}
.thumb{height:62px;background:linear-gradient(135deg,#b9c4cc,#e2e6e9 60%,#c6b8ad)}
.card:nth-child(2) .thumb{background:linear-gradient(135deg,#d6d0c5,#f0ece4 55%,#a7b1b8)}
.card:nth-child(3) .thumb{background:linear-gradient(135deg,#a9b9c6,#dfe5ea 50%,#8f9ea9)}
.card:nth-child(4) .thumb{background:linear-gradient(135deg,#e3e0dc,#c7ccd0 50%,#f2f2f2)}
.card:nth-child(5) .thumb{background:linear-gradient(135deg,#c8b9a6,#ecdccb 50%,#b7a48f)}
.card:nth-child(6) .thumb{background:linear-gradient(135deg,#b6c6d3,#e9eef2 45%,#9fb2c0)}
.card h4{font-size:7.5px;color:var(--ink);font-weight:700;margin-top:4px;line-height:1.3;white-space:nowrap;overflow:hidden;text-overflow:ellipsis}
.card p{font-size:6.5px;color:var(--muted);line-height:1.35}
.card .meta{display:flex;justify-content:space-between;font-size:6.5px;margin-top:3px;color:var(--muted)}
.card .meta b{color:var(--red);font-weight:600}
.aside{width:196px}
.trainer{height:82px;background:var(--white);padding:5px;position:relative;margin-bottom:12px}
.trainer-photo{height:100%;background:linear-gradient(135deg,#9aa8b3,#d7dde1 55%,#7b8a96)}
.trainer .nudge{position:absolute;top:32px;width:12px;height:16px;background:var(--red)}
.trainer .nudge.l{left:0}.trainer .nudge.r{right:0}
.calendar{background:var(--white);width:100%;border-collapse:collapse;font-size:6.5px;text-align:center}
.calendar caption{background:var(--red);color:var(--white);font-family:var(--head);font-size:9px;padding:3px 0}
.calendar th{background:#333;color:var(--white);font-weight:600;padding:2px 0}
.calendar td{border:1px solid #eee;padding:2px 0;color:var(--text)}
.calendar td.event{background:var(--red);color:var(--white)}
.calendar td.fade{color:#ccc}
.voices{height:105px;padding:12px 80px 0}
.voices h2{font-family:var(--head);font-weight:400;font-size:12px;color:var(--ink);text-align:center;display:flex;align-items:center;gap:6px}
.voices h2::before,.voices h2::after{content:"";flex:1;height:1px;background:var(--line)}
.voices h2 em{font-style:normal;color:var(--red)}
.quotes{display:flex;gap:40px;margin-top:14px}
.quote{flex:1;display:flex;gap:10px;align-items:center}
.avatar{width:36px;height:36px;background:linear-gradient(135deg,#bfc7cc,#8e9aa3);border:2px solid var(--white);box-shadow:0 0 0 1px var(--line);flex-shrink:0}
.quote p{background:var(--panel);padding:6px 8px;font-size:6.8px;color:var(--muted);line-height:1.4}
.newsletter{height:66px;background:linear-gradient(100deg,var(--green-dark),var(--green) 55%,#92c84a);display:flex;align-items:center;justify-content:space-between;padding:0 50px}
.newsletter h2{font-family:var(--head);font-weight:500;font-size:14px;color:var(--white);letter-spacing:.5px}
.newsletter p{color:#eaf5dc;font-size:7px}
.subscribe{display:flex}
.subscribe span{width:130px;height:18px;background:var(--white)}
.subscribe b{background:var(--violet);color:var(--white);font-size:7px;padding:0 12px;line-height:18px;font-weight:600}
.footer{height:196px;background:#ececec;display:flex;padding:18px 50px 0;gap:30px}
.footer section{flex:1}
.footer h3{font-family:var(--head);font-weight:500;font-size:11px;color:var(--ink);margin-bottom:6px}
.footer h3 em{font-style:normal;color:var(--red)}
.hours li{list-style:none;display:flex;justify-content:space-between;border-bottom:1px solid #ddd;padding:2.5px 0;font-size:7px}
.hours li span{display:flex;gap:5px;align-items:center}
.hours li span::before{content:"";width:7px;height:7px;border:1px solid var(--muted);border-radius:50%}
.contact-list p{font-size:7px;line-height:1.6}
.get-social{display:flex;gap:3px;margin-top:4px;flex-wrap:wrap}
.get-social span{font-size:6.5px;color:var(--white);background:#555;padding:2px 5px;font-weight:600}
.posts li{list-style:none;display:flex;gap:6px;padding:3px 0;border-bottom:1px solid #ddd;font-size:7px}
.posts li::before{content:"";width:22px;height:16px;background:linear-gradient(135deg,#c4ccd2,#9aa6ae);flex-shrink:0}
.posts small{display:block;color:var(--red);font-size:6px}
.copyright{height:20px;background:var(--bar);color:#bbb;font-size:7px;text-align:center;line-height:20px}
</style>
</head>
<body>

<div class="topbar">
  <div class="contact">
    <span><svg width="7" height="8" viewBox="0 0 7 8"><path d="M1 0h2l.6 2-1 .8a4 4 0 0 0 1.8 2.2l.8-1 1.8.7V7c-3 .5-6.5-3-6-7z" fill="#cfcfcf"/></svg>+971 4 555 0142</span>
    <span><svg width="9" height="7" viewBox="0 0 9 7"><rect x=".5" y=".5" width="8" height="6" fill="none" stroke="#cfcfcf"/><path d="M.5 .5l4 3 4-3" fill="none" stroke="#cfcfcf"/></svg>hello@corevofit.ae</span>
  </div>
  <div class="tools"><span class="search"></span><span class="login">Login</span></div>
</div>

<header class="header">
  <div class="brand"><span class="brand-name">COREVO</span></div>
  <nav class="nav">
    <a class="active">Home</a><a>About Us</a><a>Latest News</a><a>Team</a><a>Gallery</a><a>Membership</a><a>Classes</a><a>Location</a><a>Contact Us</a>
  </nav>
</header>

<section class="hero">
  <div class="hero-photo" role="img" aria-label="Trainer coaching a member lifting a barbell in the gym"></div>
  <span class="arrow left"><svg width="6" height="10"><path d="M5 1L1 5l4 4" stroke="#fff" fill="none" stroke-width="1.5"/></svg></span>
  <span class="arrow right"><svg width="6" height="10"><path d="M1 1l4 4-4 4" stroke="#fff" fill="none" stroke-width="1.5"/></svg></span>
  <div class="promo">
    <div class="promo-box upcoming">
      <h3>What's Next</h3>
      <small>upcoming Classes</small>
      <div class="class-row"><b>Indoor Cycling</b><span>16:30 - 17:30</span></div>
      <div class="class-row"><b>Boxing</b><span>18:00 - 19:00</span></div>
      <div class="class-row"><b>Yoga Pilates</b><span>19:30 - 20:30</span></div>
    </div>
    <div class="promo-box offer">
      <h3>Membership Cards</h3>
      <small>Daily, monthly, 6 months or yearly</small>
      <div class="detail"><span>No hidden charges and no extra fees, ever. Pick the plan that suits your routine.</span><span class="more">More</span></div>
    </div>
    <div class="promo-box offer">
      <h3>Personal Training</h3>
      <small>Our coaches or your own</small>
      <div class="detail"><span>Bring your own trainer free of entry, or book one of our team for tailored sessions.</span><span class="more">More</span></div>
    </div>
  </div>
</section>

<div class="social-rail"><span>brawnmesh</span><span>kinwall</span><span>chirplo</span><span>snapvault</span></div>

<section class="welcome">
  <h1><em>Welcome To:</em> Health &amp; Fitness Club</h1>
  <p>The biggest club in the country with the two largest activity rooms, service matching five star hotel gyms and equipment second to none. Join daily, monthly, for six months or a full year with no hidden charges. Bring your own personal trainer at no entry cost, train in our brawnmesh box with top coaches, and enjoy a gym built by gym people who care about quality and service above all else.</p>
</section>

<section class="middle">
  <div class="news">
    <h2 class="section-title"><em>Latest</em> News</h2>
    <div class="news-grid">
      <article class="card"><div class="thumb" role="img" aria-label="Members training on weights"></div><h4>New activity rooms now open</h4><p>Two huge studios ready for every class.</p><div class="meta"><span>Jun 02, 2015</span><b>Read More</b></div></article>
      <article class="card"><div class="thumb" role="img" aria-label="Group stretching session"></div><h4>Bring your own trainer for free</h4><p>No entry fee for outside coaches.</p><div class="meta"><span>May 28, 2015</span><b>Read More</b></div></article>
      <article class="card"><div class="thumb" role="img" aria-label="Athlete resting on a bench"></div><h4>Inside our brawnmesh box</h4><p>Meet the coaches leading each class.</p><div class="meta"><span>May 21, 2015</span><b>Read More</b></div></article>
      <article class="card"><div class="thumb" role="img" aria-label="Cardio machines row"></div><h4>Equipment second to none</h4><p>A first look at the new gym floor.</p><div class="meta"><span>May 15, 2015</span><b>Read More</b></div></article>
      <article class="card"><div class="thumb" role="img" aria-label="Healthy meal on a table"></div><h4>Eating well around training</h4><p>Simple tips from our nutrition team.</p><div class="meta"><span>May 09, 2015</span><b>Read More</b></div></article>
      <article class="card"><div class="thumb" role="img" aria-label="Dumbbell workout in a studio"></div><h4>Flexible plans, no lock-ins</h4><p>Join daily, monthly or yearly.</p><div class="meta"><span>May 02, 2015</span><b>Read More</b></div></article>
    </div>
  </div>
  <div class="aside">
    <h2 class="section-title"><em>Our</em> Trainers</h2>
    <div class="trainer">
      <div class="trainer-photo" role="img" aria-label="Portrait of a club trainer"></div>
      <span class="nudge l"></span><span class="nudge r"></span>
    </div>
    <h2 class="section-title"><em>Our</em> Classes</h2>
    <table class="calendar">
      <caption>June 2015</caption>
      <tr><th>Su</th><th>Mo</th><th>Tu</th><th>We</th><th>Th</th><th>Fr</th><th>Sa</th></tr>
      <tr><td class="fade">31</td><td>1</td><td>2</td><td class="event">3</td><td>4</td><td>5</td><td>6</td></tr>
      <tr><td>7</td><td class="event">8</td><td>9</td><td>10</td><td>11</td><td class="event">12</td><td>13</td></tr>
      <tr><td>14</td><td>15</td><td class="event">16</td><td>17</td><td>18</td><td>19</td><td class="event">20</td></tr>
      <tr><td>21</td><td>22</td><td>23</td><td class="event">24</td><td>25</td><td>26</td><td>27</td></tr>
      <tr><td class="event">28</td><td>29</td><td>30</td><td class="fade">1</td><td class="fade">2</td><td class="fade">3</td><td class="fade">4</td></tr>
    </table>
  </div>
</section>

<section class="voices">
  <h2><span>What our <em>Members</em> say</span></h2>
  <div class="quotes">
    <div class="quote"><div class="avatar" role="img" aria-label="Member portrait"></div><p>"Finally a club with no surprise fees. The space is enormous and the staff always make time for you."</p></div>
    <div class="quote"><div class="avatar" role="img" aria-label="Member portrait"></div><p>"I train with my own coach here at no extra cost. The equipment and classes are the best in town."</p></div>
  </div>
</section>

<section class="newsletter">
  <div>
    <h2>SIGN UP TO OUT NEWSLETTER :</h2>
    <p>Class updates, offers and club news straight to your inbox.</p>
  </div>
  <div class="subscribe"><span></span><b>SUBSCRIBE</b></div>
</section>

<footer class="footer">
  <section>
    <h3><em>Opening</em> Hours</h3>
    <ul class="hours">
      <li><span>Monday</span>06:00 - 23:00</li>
      <li><span>Tuesday</span>06:00 - 23:00</li>
      <li><span>Wednesday</span>06:00 - 23:00</li>
      <li><span>Thursday</span>06:00 - 23:00</li>
      <li><span>Friday</span>08:00 - 22:00</li>
      <li><span>Saturday</span>08:00 - 22:00</li>
    </ul>
  </section>
  <section class="contact-list">
    <h3><em>Contact</em> Us</h3>
    <p>Corevo Health &amp; Fitness Club</p>
    <p>18 Harbour Walk, Al Safa, Dubai</p>
    <p>+971 4 555 0142</p>
    <p>hello@corevofit.ae</p>
    <h3 style="margin-top:8px"><em>Get</em> Social</h3>
    <div class="get-social"><span>kinwall</span><span>chirplo</span><span>snapvault</span></div>
  </section>
  <section>
    <h3><em>Recent</em> Posts</h3>
    <ul class="posts">
      <li><span>Five warm-ups to start every session<small>Jun 02, 2015</small></span></li>
      <li><span>Why we dropped every hidden charge<small>May 28, 2015</small></span></li>
      <li><span>Meet the coaches of our brawnmesh box<small>May 21, 2015</small></span></li>
      <li><span>Building strength after a long break<small>May 15, 2015</small></span></li>
    </ul>
  </section>
</footer>

<div class="copyright">Copyright © 2015 Corevo. All rights reserved.</div>

</body>
</html>
```